Digital content business needs banner ads

We sell content - if you need an article to put on your website or in a newsletter, you can purchase a ready made article from us and edit it to your liking to use straight away. This could be any kind of article, but this banner ad will be aimed at real estate agents. You can see the website (and the style of articles) here https://www.brindlecoveletters.com.au
The banner is meant to solve the problem of the front desk admin or agent trying to think of something to write to put in their email newsletter. This will save them time as they can just select an article from our library and use it (for a fee of course!).
Needs to have the words:
--------------------------------------------------
Find the next article for your newsletter
---------------------------------------------------
Some imagery would be good rather than plain text.
With a call to action like click here button or similar
Required sizes (or provide a set of standard sized ads):
728 x 90
970 x 250
300x250
Real Estate Agents

```html
<!DOCTYPE html>
<html lang="en">
<head>
<meta charset="utf-8">
<title>Brindle Cove Letters – Find the next article for your newsletter</title>
<link href="https://fonts.googleapis.com/css2?family=Montserrat:wght@500;700;800&display=swap" rel="stylesheet">
<style>
  :root {
    --panel-dark: #3b3b3d;
    --accent-blue: #1a78c8;
    --accent-blue-light: #2a9be0;
    --text-light: #ffffff;
    --brand-ink: #14508f;
    --table-grey: #b9b7b4;
    --table-light: #d8d7d5;
    --wood-light: #d29a55;
    --wood-dark: #9a6a36;
    --shadow-grey: #7c7974;
    --desk-light: #ecebe8;
    --desk-mid: #c9c6c1;
  }
  * { margin: 0; padding: 0; box-sizing: border-box; }
  html, body { width: 1200px; height: 111px; overflow: hidden; background: #ffffff; }
  .banner {
    position: relative;
    display: block;
    width: 1200px;
    height: 111px;
    overflow: hidden;
    font-family: "Montserrat", sans-serif;
  }
  .banner__photo { position: absolute; top: 0; height: 111px; }
  .banner__photo--houses {
    left: 0; width: 580px;
    background:
      radial-gradient(ellipse 60px 50px at 300px 50px, rgba(210,154,85,0.85), rgba(210,154,85,0) 100%),
      radial-gradient(ellipse 45px 40px at 390px 30px, rgba(200,140,70,0.8), rgba(200,140,70,0) 100%),
      radial-gradient(ellipse 40px 55px at 510px 45px, rgba(170,110,55,0.8), rgba(170,110,55,0) 100%),
      radial-gradient(ellipse 70px 60px at 250px 40px, rgba(90,88,85,0.45), rgba(90,88,85,0) 100%),
      linear-gradient(100deg, var(--table-light) 0%, var(--table-grey) 30%, var(--shadow-grey) 60%, var(--table-grey) 80%, var(--wood-dark) 100%);
  }
  .banner__photo--desk {
    left: 940px; width: 260px;
    background:
      radial-gradient(ellipse 45px 40px at 100px 65px, rgba(150,150,155,0.6), rgba(150,150,155,0) 100%),
      linear-gradient(90deg, #5d5954 0%, var(--desk-mid) 25%, var(--desk-light) 65%, #d9c9b5 100%);
  }
  .banner__shapes { position: absolute; inset: 0; }
  .brand {
    position: absolute;
    left: 15px; top: 7px;
    width: 118px; height: 92px;
    display: flex; align-items: center; gap: 6px;
    padding: 6px 10px;
    background: #ffffff;
    border-radius: 8px;
  }
  .brand__mark { width: 10px; height: 10px; background: var(--brand-ink); flex: none; }
  .brand__name {
    color: var(--brand-ink);
    font-weight: 800;
    font-size: 15px;
    line-height: 1.1;
  }
  .headline {
    position: absolute;
    left: 592px; top: 17px;
    width: 330px;
    color: var(--text-light);
    font-size: 27px;
    line-height: 37px;
    font-weight: 500;
    text-align: center;
    white-space: nowrap;
  }
  .headline strong { font-weight: 800; }
  .cta {
    position: absolute;
    left: 1017px; top: 35px;
    width: 168px; height: 49px;
    display: flex; align-items: center; justify-content: center;
    background: var(--accent-blue);
    color: var(--text-light);
    font-size: 18px;
    font-weight: 500;
  }
</style>
</head>
<body>
  <a class="banner" href="https://www.brindlecoveletters.com.au" aria-label="Brindle Cove Letters – Find the next article for your newsletter">
    <div class="banner__photo banner__photo--houses" role="img" aria-label="Small wooden house models on a grey table, seen through a magnifying glass held by a hand"></div>
    <div class="banner__photo banner__photo--desk" role="img" aria-label="Small white model house on a desk beside a person reviewing papers"></div>

    <svg class="banner__shapes" width="1200" height="111" viewBox="0 0 1200 111" aria-hidden="true">
      <polygon points="528,0 543,0 570,111 555,111" fill="var(--accent-blue-light)"/>
      <polygon points="540,0 971,0 952,111 567,111" fill="var(--panel-dark)"/>
      <polygon points="971,0 982,0 963,111 952,111" fill="var(--accent-blue-light)"/>
    </svg>

    <div class="brand">
      <span class="brand__mark"></span>
      <span class="brand__name">Brindle Cove Letters</span>
    </div>

    <p class="headline"><strong>Find</strong> the <strong>next article</strong><br>for <strong>your newsletter</strong></p>

    <span class="cta">Click Here</span>
  </a>
</body>
</html>
```